Ecological Cosmetics (w/ Social Impact) Website

Dr. Wendelin Marovitz Naturprodukte KELVORA®, a small family-run ecological cosmetics “start-up” business (has been around since the mid 90s but only now beginning professionalize management), wishes to redesign its web presence, as part of a comprehensive “facelift” that will also encompass at a later stage its corporate identity (e.g. logo…).
We would like to prepare a new trilingual (later 3 additional languages will be added) website (www.kelvora7.at) that is symbiotic with web 2.0 enabled interwoven with a blog, news section, social networks integrated (e.g. preference/like buttons, Facebook), changing images and announcements appearing on first page, online payment services, mobile internet compatibility (e.g. iOS, Android, BlackBerry… thus no use of Flash, no need for a specific app), etc. and all the other significant trends in the e-commerce realm. The website should be easily and quickly accessible, fun to navigate, allow us to update it simply (through a content manager) and so “sexy” that people will want to return to the web, inform themselves of events and news, and hopefully also try our products.
Our company is based in Austria and specializes in the production of organic cosmetics in the mid-upper pricing range. We pride ourselves in offering natural cosmetics (the meaning of “natural” is relative and each person may have a different definition), with no petrochemical preservatives. Some of our products, such as the mineral salts and black mud powder from the Dead Sea cannot be obtained more naturally, unless you actually visit the area, thus retain all their properties. Our products are not medicine but the basic Dead Sea ingredients are used by spas and clinics in the area to treat many different skin, joint and bone affections. Our male and female customers (no distinction made will be made on our new website), primarily as of the ages of 25 to 65, buy KELVORA® because they:
• Care about the exterior and interior well-being
• Wish to look well cared, preserve their skin’s flexibility, natural splendor & properties
• Prefer natural skin care
• Nourish their skin with vital minerals/trace elements, protecting/treating their skin with natural ingredients
• Willing to pay more than average for natural cosmetics, looking for quality,
• Don’t mind spending about 15 minutes per week preparing a mud mask with some hot water.
• Bathe in water enriched with mineral salts
• Know or are surprised to find out that Dead Sea mud is one of the few, if not the only, naturally astringent (tenses the skin) muds in the world
• Help alleviate skin conditions (e.g. psoriasis, dermatitis, acne, eczema, pustules, oily skin ...), joint (e.g. rheumatism, arthritis ...) and cardiovascular disease.
Amongst the minerals in many of our products (particularly salt, mud), are sulfur and zinc, two naturally disinfecting and healing minerals, thus their common use in many dermatological drugs. Both salt and mud powder are completely natural, and without chemicals additives, quite important when dealing with sensitive or problematic skin, which reacts allergically to certain types of substances. The KELVORA line blends in both ingredients, enriching them with the highest-quality vitamins, essential oils and exceptional plant oils. Many of the competitors creams today use common ingredients such as petrolatum, paraffin (paraffinum liquidum), mineral oil, among others, which are derived from oil, are cheap ingredients (higher margins!) and clog pores!
To underline that this is not a chimera, there are quite a few researchers/scientists/doctors who have written articles about the benefits of the Dead Sea and its naturally occurring substances. Below are some links to abstracts of research papers, which are helpful in understanding the therapeutic potential of the black mud powder and mineral salt:
http://onlinelibrary.wiley.com/doi/10.1111/j.1365-4362.1995.tb03599.x/abstract
http://onlinelibrary.wiley.com/doi/10.1111/j.1365-4632.2005.02079.x/full
http://onlinelibrary.wiley.com/doi/10.1046/j.1365-4362.1997.00204.x/abstract
http://ard.bmj.com/content/49/2/99.short
http://www.springerlink.com/content/pv46n2p1m9p3k131/
http://onlinelibrary.wiley.com/doi/10.1111/j.1365-4632.2005.02621.x/full
http://journals.lww.com/jclinrheum/Abstract/2002/08000/Therapy_With_Mud_Compresses_for_Knee.3.aspx
http://onlinelibrary.wiley.com/doi/10.1111/j.1468-3083.1997.tb00509.x/abstract
http://onlinelibrary.wiley.com/doi/10.1046/j.1529-8019.2003.01622.x/full
http://onlinelibrary.wiley.com/doi/10.1046/j.1365-4362.1999.00583.x/full
The following links lead you to KELVORA® product data, mineral characteristics and a video of how to prepare a facial mud mask:
http://www.kelvora7.at/descargaanalisis.htm
http://www.kelvora7.at/estudio.htm
http://www.clipverse.example/watch?v=Qm4TzLp8WxR
We would like to convey, through our striking and attractive new graphic design, our values to potential clients: quality, 100% natural product, effectiveness, seriousness, confidence, respect for the environment, people, animals (the products are not tested on animals), all of which has a price (they are not cheap!). To put our money where our mouth is and contribute to transforming our planet into a better place, we are discussing with NGOs donating a percentage of certain product sales to support their causes.
Our web currently is available in 3 languages: German, Spanish and English, however, we plan to expand it by another 2 to 3 languages (Portuguese, Russian, Chinese). We are looking for a graphic design that will communicate our values and captivate people's attention, thereby helping us increase sales, projecting a solid and elegant image of reliability, effectiveness, simplicity and trust. Although we are not, and do not wish to, market our products as medicine, we do want to express, through our new graphic design, the fact that these products can be used to treat all types of skin, mitigate certain skin affections (e.g. psoriasis, dermatitis, acne, eczema, sensitive skin), and, depending on each organism’s reaction, different ailments (e.g. arthritis, rheumatism), although they won’t cure them (they can alleviate!).
To get an idea of our company, I invite you to explore our website, www.kelvora7.at, and see photos of our products. Attached please find some photos of our products, including the newly designed black mud powder box. We would like to create a unified corporate image. At this point we know that some, if not all, packages do not convey quality nor our values – this is something we wish to gradually change as each products’ graphic design and packaging gets renewed, consistent with the new brand image. This is work-in-progress and will be addressed as the company grows and has the financial capacity to invest in new design and packaging. We are advancing step by step.
Content-wise, we would provide you with product photos, and the texts to be inserted, but would like to complement these with other photos (e.g. from photobanks that include images of the Dead Sea, beaches, plants, nature…). The design should quickly associate the Internet user/visitor of our website with our values and the idea of quality products. A content manager will be used to update and modify our product portfolio.
Although some people will find us by typing into their web browser the address of our website, many will use search engines to locate us on the WWW. For this purpose, it would also be important that kelvora7.at’s different webpages can be referenced, searched for keywords and allow analysis of webtraffic (e.g. Google Analytics…).
Two colors are being used in our packages, green Pantone No. 326 and blue Pantone No. 072. We are completely flexible in terms of colors.
We hope you find the project interesting. Any questions, please do not hesitate to contact us. Thank you very much for your time, recommendations and proposals. Ideally we can close this project in about 14 days.
Information to be considered and/or included in the design:
• The web will feature an e-commerce shop, whose design should also be included in your creative proposal.
• Cosmetics tend to be divided along the lines of skin types, yet as the KELVORA line is still quite small, we have decided to divide it along treatment areas: hair, face, body. Each product is indicated for a particular skin type.
• Keyword Search box for the entire website
The current web is slow, all in Flash, difficult to navigate, has too many intermediate stages, does not offer a keyword search function, nor incorporate any web 2.0 features. Furthermore, it is more difficult to find and index in search engines as none of the pages have specific web addresses. In terms of intermediate pages, these should be eliminated shortening the time the user needs to obtain the desired information (e.g. the landing page where you choose sex & language, followed by drop of water being filled up), such that the visitor is directly lead to the main page (equal to the landing page). At first glance, the blue background and the drop of water filling up may lead the visitor to believe we are dedicated to something with water, perhaps even plumbing or purification services – such an impression must be avoided. Perhaps one of the ways to analyze all the aspects to be incorporated is an evaluation of our current web’s weaknesses and prepare a design where those are all addressed.
Target Market(s)
Male & female customers, approx. age 18-65, who care about their exterior and interior well being, “worried” about their skin, willing to pay more tha
Industry/Entity Type
Graphic Design
Requirements
Must have
- • The web will also feature a blog and an e-commerce shop, whose designs should also be included in your creative proposal.
• Address current and future languages
Content-wise, we will product photos, and the texts to be inserted, but would like to complement these with other photos (e.g. from photobanks that include images of the Dead Sea, beaches, plants, nature…). The design should quickly associate the Internet user/visitor of our website with our values and the idea of quality products. A content manager will be used to update and modify our product portfolio, as well as effects announcements on the landing page.

```html
<!DOCTYPE html>
<html lang="en">
<head>
<meta charset="utf-8">
<title>KELVORA® Naturprodukte – Home</title>
<link rel="stylesheet" href="https://fonts.googleapis.com/css2?family=Roboto+Condensed:wght@400;700&family=Cabin:wght@400;600&family=Arimo:wght@400&display=swap">
<style>
  :root {
    --cyan: #1aa9d8;
    --navy: #13206a;
    --slate: #3d4f86;
    --lime: #c5dc1e;
    --border: #e3e6ea;
    --text: #222;
    --muted: #888;
    --tab-bg: #eef7fc;
  }
  * { box-sizing: border-box; margin: 0; padding: 0; }
  html, body { width: 983px; height: 1200px; overflow: hidden; background: #fff; }
  body { position: relative; font-family: "Arimo", Arial, sans-serif; color: var(--text); }

  .lang-switch { position: absolute; top: 13px; right: 28px; font: 400 12px "Roboto Condensed", sans-serif; color: #555; }
  .lang-switch b { color: #111; font-weight: 700; }

  .brand-dot { position: absolute; left: 34px; top: 58px; width: 22px; height: 22px; border-radius: 50%; background: var(--lime); }

  .main-nav { position: absolute; top: 84px; left: 31px; right: 34px; display: flex; justify-content: space-between; list-style: none; }
  .main-nav li { font: 400 13px "Roboto Condensed", sans-serif; color: var(--cyan); text-transform: uppercase; }

  .hero { position: absolute; left: 11px; top: 111px; width: 961px; height: 383px; border: 1px solid var(--border); box-shadow: 0 1px 3px rgba(0,0,0,.08); background: #fff; overflow: hidden; }
  .hero-mark { position: absolute; left: 200px; top: 78px; width: 140px; height: 140px; border-radius: 50%; border: 2px solid var(--navy); display: flex; align-items: center; justify-content: center; font: 600 20px "Cabin", sans-serif; color: var(--navy); }
  .hero-lede { position: absolute; left: 28px; top: 260px; width: 540px; font: 400 17px/1.25 "Cabin", sans-serif; color: var(--slate); }
  .hero-photo { position: absolute; right: 20px; top: 8px; width: 383px; height: 366px; background: radial-gradient(ellipse at 45% 55%, #f0d2bd 0%, #e9d9cf 35%, #f6f4f2 70%, #fff 100%); }

  .range { position: absolute; left: 11px; top: 512px; width: 961px; height: 176px; background: linear-gradient(#f3f9fd, #eaf5fb); }
  .range-tabs { position: absolute; left: 17px; top: 10px; display: flex; list-style: none; }
  .range-tabs li { font: 400 11px "Roboto Condensed", sans-serif; color: var(--navy); text-transform: uppercase; padding: 8px 0 8px 0; margin-right: 50px; }
  .range-tabs li.is-active { color: var(--cyan); background: #fff; padding: 8px 18px; margin-right: 28px; border: 1px solid var(--border); border-bottom: none; }
  .range-panel { position: absolute; left: 15px; top: 36px; width: 912px; height: 126px; background: #fff; border: 1px solid var(--border); }
  .product { position: absolute; top: 16px; display: flex; }
  .product-photo { width: 96px; height: 96px; border-radius: 50%; background: linear-gradient(#1a7d86 0%, #3aa5ad 40%, #b8c7d2 60%, #8fa0b4 100%); box-shadow: 0 2px 4px rgba(0,0,0,.15); flex: none; }
  .product-copy { margin-left: 18px; margin-top: 30px; }
  .product-copy h3 { font: 400 12px "Cabin", sans-serif; color: var(--navy); letter-spacing: .3px; margin-bottom: 12px; }
  .product-copy p { font: 600 10px/1.4 "Cabin", sans-serif; color: var(--navy); width: 150px; }

  .welcome { position: absolute; left: 33px; top: 712px; width: 656px; }
  .welcome h1 { font: 400 24px "Roboto Condensed", sans-serif; color: var(--slate); margin-bottom: 12px; }
  .welcome p { font-size: 11px; line-height: 17.5px; text-align: justify; margin-bottom: 17px; }

  .beauty { position: absolute; left: 760px; top: 716px; width: 130px; text-align: center; }
  .beauty em { font: italic 400 17px "Cabin", sans-serif; color: var(--cyan); }
  .beauty-mark { margin: 14px auto 0; width: 96px; height: 96px; border-radius: 50%; border: 2px solid var(--navy); display: flex; align-items: center; justify-content: center; font: 600 14px "Cabin", sans-serif; color: var(--navy); }

  .testimonials { position: absolute; left: 11px; top: 955px; width: 481px; height: 133px; border: 1px solid var(--border); }
  .testimonials h2 { position: absolute; left: 12px; top: 17px; font: 400 13px "Cabin", sans-serif; color: var(--cyan); }
  .testimonial-photo { position: absolute; left: 15px; top: 47px; width: 72px; height: 48px; background: linear-gradient(90deg, #e7c9b4, #f3e2d6); }
  .testimonial-quote { position: absolute; left: 96px; top: 51px; width: 340px; font: 400 10px/1.6 "Cabin", sans-serif; color: #555; }
  .testimonial-author { display: block; text-align: right; font-weight: 600; color: var(--navy); }

  .follow { position: absolute; left: 515px; top: 955px; width: 457px; height: 133px; border: 1px solid var(--border); }
  .follow-band { position: absolute; left: 8px; top: 8px; width: 440px; height: 116px; background: var(--lime); }
  .follow-mark { position: absolute; left: 14px; top: 10px; width: 96px; height: 96px; border-radius: 50%; border: 2px solid rgba(255,255,255,.45); display: flex; align-items: center; justify-content: center; font: 600 14px "Cabin", sans-serif; color: rgba(255,255,255,.6); }
  .follow-label { position: absolute; left: 210px; top: 53px; font: 400 16px "Cabin", sans-serif; color: #fff; }
  .social { position: absolute; top: 40px; width: 40px; height: 40px; border-radius: 6px; background: #fff; }

  .site-footer { position: absolute; left: 567px; top: 1104px; font: 400 9px/17px "Cabin", sans-serif; color: var(--muted); }
</style>
</head>
<body>
  <div class="lang-switch"><b>EN</b> | DE | ES</div>
  <span class="brand-dot"></span>
  <ul class="main-nav">
    <li>Home</li><li>Kelvora</li><li>Dead Sea</li><li>Aromatherapy</li><li>Facial Care</li><li>Body Care</li><li>Hair Care</li><li>Spas</li><li>Contact</li>
  </ul>

  <section class="hero">
    <div class="hero-mark">KELVORA®</div>
    <p class="hero-lede">Lorem ipsum dolor sit amet, consectetur adipiscing elit. Etiam vel rutrum elit. Duis elit quam, eleifend eget sollicitudin sed, sodales vitae tortor.</p>
    <div class="hero-photo" role="img" aria-label="Photo of a woman in a white towel holding a calla lily"></div>
  </section>

  <section class="range">
    <ul class="range-tabs">
      <li class="is-active">Dead Sea</li><li>Aromatherapy</li><li>Facial Care</li><li>Body Care</li><li>Hair Care</li><li>Spas</li>
    </ul>
    <div class="range-panel">
      <div class="product" style="left:8px">
        <div class="product-photo" role="img" aria-label="Product photo: jar of Dead Sea mineral salt"></div>
        <div class="product-copy"><h3>LOREM IPSUM</h3><p>dolor sit amet, consectetur adipi-scing elit. Etiam vel rutrum elit.</p></div>
      </div>
      <div class="product" style="left:292px">
        <div class="product-photo" role="img" aria-label="Product photo: jar of Dead Sea mineral salt"></div>
        <div class="product-copy"><h3>LOREM IPSUM</h3><p>dolor sit amet, consectetur adipi-scing elit. Etiam vel rutrum elit.</p></div>
      </div>
      <div class="product" style="left:599px">
        <div class="product-photo" role="img" aria-label="Product photo: jar of Dead Sea mineral salt"></div>
        <div class="product-copy"><h3>LOREM IPSUM</h3><p>dolor sit amet, consectetur adipi-scing elit. Etiam vel rutrum elit.</p></div>
      </div>
    </div>
  </section>

  <section class="welcome">
    <h1>WELCOME</h1>
    <p>Lorem ipsum dolor sit amet, consectetur adipiscing elit. Etiam vel rutrum elit. Duis elit quam, eleifend eget sollicitudin sed, sodales vitae tortor. Aenean venenatis, dui eget rutrum elementum, ipsum quam mollis libero, nec molestie nulla diam eu neque. Duis vestibulum massa sit amet nunc hendrerit feugiat ac sed diam.</p>
    <p>Proin nibh justo, fermentum vel tristique vitae, placerat ut leo. Quisque sodales bibendum risus ac vulputate. Praesent nisi dui, tincidunt luctus pulvinar id, sodales sit amet orci.</p>
    <p>Aenean id consequat tellus. Nulla posuere vehicula lacinia. Donec sit amet erat quam. Ut pellentesque, ante faucibus adipiscing iaculis, mi justo facilisis elit, vel placerat magna erat nec magna. Vestibulum eget est ligula. Cras et commodo nibh. Morbi nulla odio, porta a tincidunt in, faucibus a felis. Vestibulum lobortis tincidunt pretium. Etiam turpis dolor, condimentum ac tempor sit amet, ornare ac leo.</p>
  </section>

  <aside class="beauty">
    <em>the beauty of</em>
    <div class="beauty-mark">KELVORA®</div>
  </aside>

  <section class="testimonials">
    <h2>Testimonials</h2>
    <div class="testimonial-photo" role="img" aria-label="Photo of a smiling couple"></div>
    <p class="testimonial-quote">“Lorem ipsum dolor sit amet, consectetur adipiscing elit. Etiam vel rutrum elit. Duis elit quam, eleifend eget sollicitudin sed, sodales vitae tortor.”<span class="testimonial-author">- Mira</span></p>
  </section>

  <section class="follow">
    <div class="follow-band">
      <div class="follow-mark">KELVORA®</div>
      <span class="follow-label">follow us on</span>
      <span class="social" style="left:316px" aria-label="Social network link"></span>
      <span class="social" style="left:363px" aria-label="Social network link"></span>
    </div>
  </section>

  <footer class="site-footer">
    Copyright ©2012 by KELVORA NATURPRODUKTE DR. WENDELIN MAROVITZ. All rights reserved.<br>
    www.kelvora7.at &nbsp; Email: info@kelvora7.at<br>
    Visit KELVORA® and learn more about the skin
  </footer>
</body>
</html>
```